New web design for a service provider in the medical field

We are looking for a new design for our website. We are a company that repairs and sells medical endoscopes. Our customers include doctors and hospitals. Our current website can be found at https://lumavex.de/en/lumavex-english.
We need a new web design (without programming) for the following 3 pages:
-Startpage https://lumavex.de/en/lumavex-english/
-Used endoscopes https://lumavex.de/en/used-endoscopes/
-Purchase https://lumavex.de/en/purchase/
The design should be modern and stylish.
The blue color of the logo should be reflected on the page, but not too intrusive.
I have uploaded the images from the header. If more images are needed, let me know and I will upload them.

Target Market(s)
Doctors and hospitals

```html
<!DOCTYPE html>
<html lang="en">
<head>
<meta charset="utf-8">
<title>Lumavex – Endoscope Repair &amp; Sale</title>
<link href="https://fonts.googleapis.com/css2?family=Poppins:wght@400;500;600;700&display=swap" rel="stylesheet">
<style>
:root{
  --blue:#2a9fd8;
  --blue-dark:#1d86bd;
  --navy:#2b3f54;
  --navy-deep:#24364a;
  --ink:#1f3a52;
  --text:#5c6b78;
  --line:#e3e8ee;
  --white:#fff;
  --orvalis:#0b4f93;
  --penrix:#e03426;
  --fujora:#000;
}
*{box-sizing:border-box;margin:0;padding:0}
html,body{width:1200px;height:4225px;overflow:hidden}
body{font-family:'Poppins',sans-serif;color:var(--ink);background:var(--white);position:relative}
.container{width:1080px;margin:0 auto;position:relative}
section,header,footer{position:relative;overflow:hidden}
.title{text-align:center;font-weight:600;font-size:36px;color:var(--ink)}
.title-rule{display:block;width:56px;height:2px;background:var(--blue);margin:14px auto 0;position:relative}
.title-rule::after{content:"";position:absolute;left:50%;top:-3px;width:8px;height:8px;margin-left:-4px;border-radius:50%;background:var(--blue)}
.btn{display:inline-block;font-weight:600;font-size:13px;text-transform:uppercase;color:var(--white);background:var(--blue);padding:12px 20px;border-radius:3px;text-decoration:none}
.btn-pill{border-radius:22px;box-shadow:0 6px 14px rgba(42,159,216,.35)}

/* header */
.site-header{height:105px;background:var(--white)}
.brand{position:absolute;left:60px;top:30px;display:flex;align-items:center;gap:8px;font-weight:600;font-size:17px;color:var(--navy)}
.brand-dot{width:12px;height:12px;border-radius:50%;background:var(--blue)}
.topbar{position:absolute;left:377px;top:0;right:0;height:36px;background:var(--blue);border-bottom-left-radius:20px;display:flex;align-items:center;padding-left:28px;font-size:12.5px;color:var(--white);gap:22px}
.topbar .contact{display:flex;align-items:center;gap:8px;font-weight:500}
.topbar .icon{width:20px;height:20px;border-radius:50%;background:var(--white);display:flex;align-items:center;justify-content:center}
.topbar .links{margin-left:24px;display:flex;gap:30px}
.topbar .lang{margin-left:auto;width:52px;height:36px;background:var(--blue-dark);display:flex;align-items:center;justify-content:center;margin-right:28px}
.nav{position:absolute;right:60px;top:60px;display:flex;gap:45px;font-size:13px;color:var(--ink)}
.nav .active{color:var(--blue)}

/* hero */
.hero{height:495px;background:linear-gradient(100deg,#3a5266 0%,#4b6275 45%,#5f7585 100%)}
.hero-photo{position:absolute;inset:0;background:radial-gradient(circle at 78% 45%,rgba(235,240,243,.55) 0,rgba(235,240,243,.1) 30%,transparent 45%)}
.hero-copy{position:absolute;left:58px;top:120px;color:var(--white)}
.hero-copy h1{font-size:50px;line-height:58px;font-weight:600}
.hero-copy h1 span{color:var(--blue)}
.hero-copy p{font-size:16px;line-height:26px;margin:18px 0 26px;width:360px}

/* future */
.future{height:663px}
.future .title{padding-top:64px}
.future .lead{width:700px;margin:28px auto 0;text-align:center;font-size:13.5px;line-height:23px;color:var(--text)}
.future .circle{position:absolute;left:8px;top:187px;width:172px;height:172px;border-radius:50%;background:#cfe8f6}
.future .photo{position:absolute;left:60px;top:259px;width:494px;height:328px;border-radius:10px;background:linear-gradient(135deg,#e9edf0,#c9d2d9)}
.future .text{position:absolute;left:613px;top:262px;width:460px}
.future h2{font-size:33px;line-height:44px;font-weight:500}
.future .rule{width:56px;height:2px;background:var(--blue);margin:18px 0 22px}
.future .text p{font-size:13px;line-height:22px;color:var(--text);margin-bottom:4px}

/* what we do */
.services{height:688px;background:var(--navy)}
.services .title{color:var(--white);padding-top:68px}
.services .cards{display:flex;gap:23px;margin-top:38px}
.card{width:345px;height:456px;background:var(--white);border-radius:4px;overflow:hidden;text-align:center}
.card .media{height:231px}
.card h3{font-size:17px;font-weight:600;margin:22px 0 16px}
.card p{font-size:12.2px;line-height:21.5px;color:var(--text);padding:0 26px;height:88px}
.card .link{display:block;font-size:12.5px;font-weight:500;margin-top:16px;color:var(--ink)}

/* brand bar */
.makers{height:74px;display:flex}
.maker{flex:1;display:flex;align-items:center;justify-content:space-between;padding:0 60px;color:var(--white);font-weight:600;font-size:17px}
.maker.o{background:var(--orvalis)}.maker.p{background:var(--penrix)}.maker.f{background:var(--fujora)}

/* outcome */
.outcome{height:481px}
.outcome .title{padding-top:64px}
.features{display:flex;gap:10px;margin-top:34px}
.feature{width:172px;height:246px;border:1px solid var(--line);border-radius:4px;padding:28px 14px 0}
.feature.highlight{border:2px solid var(--blue)}
.feature svg{display:block;margin-bottom:14px}
.feature h4{font-size:14.5px;font-weight:600;line-height:22px;margin-bottom:10px}
.feature p{font-size:12px;line-height:22px;color:var(--text)}

/* cta */
.cta{height:164px;background:var(--blue)}
.cta .arc{position:absolute;left:-60px;top:-60px;width:440px;height:440px;border-radius:50%;background:#3aa9de}
.cta .scope{position:absolute;left:95px;top:14px;width:165px;height:150px;border-radius:80px 80px 0 0;background:linear-gradient(160deg,#2a3642,#4a5866)}
.cta h2{position:absolute;left:469px;top:38px;color:var(--white);font-size:34px;font-weight:600}
.cta p{position:absolute;left:470px;top:104px;color:var(--white);font-size:13px}
.cta .btn{position:absolute;left:934px;top:62px;background:var(--navy);padding:11px 24px}

/* decision */
.decision{height:905px;background:var(--navy)}
.decision .title{color:var(--white);padding-top:68px}
.grid{display:grid;grid-template-columns:repeat(3,346px);gap:23px 21px;margin-top:40px}
.tile{height:300px;border:1px solid #3f5a73;border-radius:3px;background:var(--navy-deep);padding:34px 30px 0;color:var(--white)}
.tile svg{display:block;margin-bottom:20px}
.tile h4{font-size:19px;font-weight:500;line-height:28px;margin-bottom:12px}
.tile p{font-size:12.2px;line-height:20px;color:#d9e2ea}
.decision .more{text-align:center;margin-top:30px}

/* help */
.help{height:312px;text-align:center}
.help .title{padding-top:96px}
.help .btn{margin-top:30px}

/* footer */
.site-footer{height:287px;background:var(--navy)}
.footer-brand{position:absolute;left:66px;top:70px;display:flex;align-items:center;gap:8px;color:var(--white);font-weight:600;font-size:15px}
.social{position:absolute;left:80px;top:124px;display:flex;gap:24px}
.social span{width:30px;height:30px;border-radius:50%;background:var(--blue)}
.social span+span{background:transparent;border:2px solid var(--blue);width:18px;height:18px;margin-top:6px;border-radius:5px}
.fcol{position:absolute;top:56px;color:var(--white)}
.fcol h5{color:var(--blue);font-size:18px;font-weight:500;margin-bottom:10px}
.fcol li{list-style:none;font-size:12.5px;line-height:22.5px}
.fcol li::before{content:"•";margin-right:7px}
.fcontact{position:absolute;left:936px;top:56px;color:var(--white)}
.fcontact h5{color:var(--blue);font-size:18px;font-weight:500;margin-bottom:14px}
.frow{display:flex;gap:14px;align-items:flex-start;margin-bottom:14px;font-size:13px;line-height:20px}
.frow .ico{width:30px;height:30px;border-radius:50%;background:var(--blue);flex:none;display:flex;align-items:center;justify-content:center}
.frow strong{font-weight:600;font-size:14px;line-height:30px}
.frow u{line-height:30px}
.copyright{height:51px;background:var(--blue);color:var(--white);text-align:center;font-size:11.5px;font-weight:500;line-height:51px}
</style>
</head>
<body>

<header class="site-header">
  <div class="brand"><span class="brand-dot"></span>Lumavex</div>
  <div class="topbar">
    <span class="contact"><span class="icon"><svg width="11" height="11" viewBox="0 0 24 24"><path fill="#2a9fd8" d="M6.6 10.8a15 15 0 006.6 6.6l2.2-2.2c.3-.3.7-.4 1-.2 1.1.4 2.3.6 3.6.6.6 0 1 .4 1 1V20c0 .6-.4 1-1 1A17 17 0 013 4c0-.6.4-1 1-1h3.5c.6 0 1 .4 1 1 0 1.3.2 2.5.6 3.6.1.3 0 .7-.2 1z"/></svg></span>+49 4020 555 180-0</span>
    <span class="contact"><span class="icon"><svg width="11" height="11" viewBox="0 0 24 24"><path fill="#2a9fd8" d="M2 5h20v14H2zM2 5l10 8 10-8" stroke="#fff" stroke-width="1.5"/></svg></span>info@lumavex.de</span>
    <span class="links"><span>Pick-Up Order</span><span>About Us</span><span>Contact Us</span></span>
    <span class="lang">En ⌄</span>
  </div>
  <nav class="nav">
    <span class="active">• Home</span><span>Endoscope Repair</span><span>Used Endoscopes</span><span>Endoscopy Systems</span><span>Accessories</span><span>Purchase</span>
  </nav>
</header>

<section class="hero">
  <div class="hero-photo" role="img" aria-label="Two medical technicians inspecting a flexible endoscope, handpiece in the foreground"></div>
  <div class="hero-copy">
    <h1>Put Your Endoscope<br>In <span>Reliable Hands!</span></h1>
    <p>Lorem ipsum dolor sit amet, consectetuer adipiscing elit, sed diam nonummy.</p>
    <a class="btn">Request Pick Up Now!</a>
  </div>
</section>

<section class="future">
  <h2 class="title">Your Future - Our Service</h2>
  <span class="title-rule"></span>
  <p class="lead">Lumavex GmbH is specialised in the repair and sale of Orvalis, Penrix and Fujora flexible medical endoscopes. As a service-oriented company, we are at your side with our knowledge and skills!</p>
  <div class="circle"></div>
  <div class="photo" role="img" aria-label="Technician in a white coat working at an endoscopy tower with monitor"></div>
  <div class="text">
    <h2>Endoscope Repairs And Second Hand Endoscopes</h2>
    <div class="rule"></div>
    <p>Lumavex is a privileged partner for the start-up facility or optimisation of existing healthcare facilities, doctor's offices and hospitals. The quality and reliability of our products and our offered service are our best advertisement!</p>
    <p>Lumavex is a privileged partner for the start-up facility or optimisation of existing healthcare facilities, doctor's offices and hospitals. The quality and reliability of our products and our offered service are our best advertisement!</p>
  </div>
</section>

<section class="services">
  <h2 class="title">What We Do</h2>
  <span class="title-rule"></span>
  <div class="container cards">
    <article class="card">
      <div class="media" role="img" aria-label="Gloved hands holding an endoscope" style="background:linear-gradient(135deg,#dfe5ea,#a9b5bf)"></div>
      <h3>Repair - Endoscope Repair Service</h3>
      <p>Manufacturer-independent we repair and maintain endoscopes, individual components (e.g. processors or light sources), accessories and peripherals of the manufacturers Orvalis, Penrix and Fujora.</p>
      <span class="link">REPAIR REQUEST →</span>
    </article>
    <article class="card">
      <div class="media" role="img" aria-label="Endoscope and parts laid out on a turquoise cloth" style="background:linear-gradient(135deg,#e3b46a,#3a8d97)"></div>
      <h3>Sale - Used Endoscopes</h3>
      <p>Our regular stock includes refurbished gastroscopes, coloscopes, bronchoscopes, cystoscopes and duodenoscopes from the well-known manufacturers Orvalis, Penrix and Fujora.</p>
      <span class="link">PURCHASE REQUEST →</span>
    </article>
    <article class="card">
      <div class="media" role="img" aria-label="Close-up of an endoscope control section" style="background:linear-gradient(135deg,#e6e8ea,#6f7880)"></div>
      <h3>Purchase - Used Endoscopes</h3>
      <p>We are very interested in buying your old endoscopes – even defective and dismantled! We offer fair conditions! Please contact us for a purchase offer!</p>
      <span class="link">SELL DEVICE →</span>
    </article>
  </div>
</section>

<div class="makers">
  <div class="maker o">ORVALIS<span>→</span></div>
  <div class="maker p">PENRIX<span>→</span></div>
  <div class="maker f">FUJORA<span>→</span></div>
</div>

<section class="outcome">
  <h2 class="title">Cause The Outcome Matters!</h2>
  <span class="title-rule"></span>
  <div class="container features">
    <div class="feature"><svg width="44" height="44" viewBox="0 0 44 44" fill="none" stroke="#1f3a52" stroke-width="2"><rect x="6" y="10" width="32" height="30"/><path d="M12 16h4M20 16h4M28 16h4M12 24h4M20 24h4M28 24h4" stroke="#2a9fd8"/></svg><h4>One Company For Everyone</h4><p>We are a service provider for doctors and hospitals!</p></div>
    <div class="feature"><svg width="44" height="44" viewBox="0 0 44 44" fill="none" stroke="#1f3a52" stroke-width="2"><rect x="6" y="4" width="32" height="12" rx="2" stroke="#2a9fd8"/><circle cx="14" cy="26" r="4"/><circle cx="30" cy="26" r="4"/><path d="M6 40c0-5 4-8 8-8s8 3 8 8M22 40c0-5 4-8 8-8s8 3 8 8"/></svg><h4>Experience Characterises Us</h4><p>Our team has many years of experience in the business field!</p></div>
    <div class="feature"><svg width="44" height="44" viewBox="0 0 44 44" fill="none" stroke="#1f3a52" stroke-width="2"><path d="M16 40V12a6 6 0 0112 0v28"/><rect x="13" y="34" width="6" height="6" stroke="#2a9fd8"/></svg><h4>The Product Is Close To Our Hearts</h4><p>We repair and sell second hand, flexible endoscopes!</p></div>
    <div class="feature highlight"><svg width="44" height="44" viewBox="0 0 44 44" fill="none" stroke="#1f3a52" stroke-width="2"><path d="M22 4l16 6v12c0 10-8 16-16 18C14 38 6 32 6 22V10z"/><path d="M15 22l5 5 9-10" stroke="#2a9fd8"/></svg><h4>Guaranteed Service</h4><p>You receive a six-month warranty on all repairs!</p></div>
    <div class="feature"><svg width="44" height="44" viewBox="0 0 44 44" fill="none" stroke="#1f3a52" stroke-width="2"><circle cx="22" cy="17" r="12"/><path d="M16 28l-4 12 10-4 10 4-4-12"/><path d="M17 17l4 4 7-7" stroke="#2a9fd8"/></svg><h4>Quality Not Quantity</h4><p>Reliability and durability instead of inferior replacements!</p></div>
    <div class="feature"><svg width="44" height="44" viewBox="0 0 44 44" fill="none" stroke="#1f3a52" stroke-width="2"><circle cx="22" cy="22" r="16"/><circle cx="22" cy="22" r="7" stroke="#2a9fd8"/></svg><h4>Services For Everyone</h4><p>Our service includes the manufacturers Orvalis, Penrix and Fujora!</p></div>
  </div>
</section>

<section class="cta">
  <div class="arc"></div>
  <div class="scope" role="img" aria-label="Endoscope control handle"></div>
  <h2>Faulty Endoscope?</h2>
  <p>We ensure quick and smooth repairs! Simple place a</p>
  <a class="btn">Pick-Up Order</a>
</section>

<section class="decision">
  <h2 class="title">Your Decision For Your Future</h2>
  <span class="title-rule"></span>
  <div class="container grid">
    <div class="tile"><svg width="100" height="90" viewBox="0 0 100 90" fill="none" stroke="#2a9fd8" stroke-width="3"><circle cx="60" cy="45" r="30"/><path d="M5 30h25M10 45h20M5 60h25"/></svg><h4>Fast Repairs</h4><p>Keep potential disruptions in your doctor's office or in your hospital at minimum as a result of optimized processes and highly qualified specialists in our company</p></div>
    <div class="tile"><svg width="100" height="90" viewBox="0 0 100 90" fill="none" stroke="#2a9fd8" stroke-width="3"><circle cx="45" cy="45" r="40"/><circle cx="45" cy="45" r="26"/><path d="M45 30v30M52 36c-4-4-14-3-14 3s14 5 14 11-10 7-14 3"/></svg><h4>Highly Cost Efficient</h4><p>Benefit from our first class recommendations and implementation by our experienced staff. Our goals is to find the best solutions together with you at the best lowest price point.</p></div>
    <div class="tile"><svg width="100" height="90" viewBox="0 0 100 90" fill="none" stroke="#2a9fd8" stroke-width="3"><rect x="8" y="30" width="80" height="56"/><circle cx="48" cy="20" r="14"/><path d="M48 12v16M40 20h16M20 44h12M40 44h16M64 44h12M20 60h12M64 60h12M40 62h16v24H40z"/></svg><h4>On-site Service</h4><p>We will gladly pay you a visit to to carry out analysis and repairs on site. Due to our many years of experience – it doesn't get any faster (whigleithin a 250 km range)</p></div>
    <div class="tile"><svg width="100" height="90" viewBox="0 0 100 90" fill="none" stroke="#2a9fd8" stroke-width="3"><circle cx="52" cy="38" r="18"/><path d="M44 20l4-12h8l4 12M4 70l20-10h24l30-10M4 86l28-6 50-24"/></svg><h4>Loan Equipment Service</h4><p>Use our service of high-quality loan devices during the downtime of your defective endoscope (limited to stock)</p></div>
    <div class="tile"><svg width="100" height="90" viewBox="0 0 100 90" fill="none" stroke="#2a9fd8" stroke-width="3"><circle cx="45" cy="45" r="40"/><circle cx="45" cy="45" r="32"/><rect x="32" y="24" width="26" height="40"/><path d="M38 36h14M38 44h14M38 52h14M16 18l58 54"/></svg><h4>Without A Maintenance Contract</h4><p>No subscription or other maintenance contract, but one-time and sustainable repair work</p></div>
    <div class="tile"><svg width="110" height="90" viewBox="0 0 110 90" fill="none" stroke="#2a9fd8" stroke-width="3"><circle cx="55" cy="30" r="26"/><circle cx="55" cy="30" r="19"/><path d="M55 20v20M35 54l-6 18h52l-6-18M8 72h94v14H8z"/></svg><h4>First Class Service</h4><p>Our clients always come first!</p></div>
  </div>
  <div class="more"><a class="btn btn-pill">Learn More About Lumavex!</a></div>
</section>

<section class="help">
  <h2 class="title">How Can We Help You?</h2>
  <a class="btn btn-pill">Send Us A Message!</a>
</section>

<footer class="site-footer">
  <div class="footer-brand"><span class="brand-dot"></span>Lumavex</div>
  <div class="social"><span></span><span></span></div>
  <div class="fcol" style="left:287px"><h5>Company</h5><ul><li>Home</li><li>Endoscope Repair</li><li>Used Endoscopes</li><li>Endoscopy Systems</li><li>Accessories</li><li>Purchase</li></ul></div>
  <div class="fcol" style="left:527px"><h5>More</h5><ul><li>Pick-Up Order</li><li>About Us</li><li>Contact Us</li></ul></div>
  <div class="fcol" style="left:733px"><h5>Support</h5><ul><li>Information</li><li>TOS</li><li>Copyrights</li><li>Privacy Policy</li></ul></div>
  <div class="fcontact">
    <h5>Contact Details</h5>
    <div class="frow"><span class="ico"><svg width="14" height="14" viewBox="0 0 24 24"><path fill="#fff" d="M6.6 10.8a15 15 0 006.6 6.6l2.2-2.2c.3-.3.7-.4 1-.2 1.1.4 2.3.6 3.6.6.6 0 1 .4 1 1V20c0 .6-.4 1-1 1A17 17 0 013 4c0-.6.4-1 1-1h3.5c.6 0 1 .4 1 1 0 1.3.2 2.5.6 3.6.1.3 0 .7-.2 1z"/></svg></span><strong>040-555-0192</strong></div>
    <div class="frow"><span class="ico"><svg width="14" height="14" viewBox="0 0 24 24" fill="none" stroke="#fff" stroke-width="2"><rect x="3" y="5" width="18" height="14"/><path d="M3 5l9 8 9-8"/></svg></span><u>info@lumavex.de</u></div>
    <div class="frow"><span class="ico"><svg width="14" height="14" viewBox="0 0 24 24" fill="none" stroke="#fff" stroke-width="2"><path d="M12 22s7-7 7-12a7 7 0 00-14 0c0 5 7 12 7 12z"/><circle cx="12" cy="10" r="2.5"/></svg></span><span>Lindenweg 12<br>21390 Feldmark<br>Germany</span></div>
  </div>
</footer>
<div class="copyright">© Lumavex - 2022. All Rights Reserved.</div>

</body>
</html>
```